Website re-design for Brightmoor LLC website ( has existing website )

Looking to do a complete re-design of Brightmoorllc. The existing website is dated and built in wordpress. The new website will not be wordpress. The project folder includes an overview.txt file with details on the project. The file also contains a list of websites that he/she likes which I am sure is very helpful .
Number of Pages Required
1 page

```html
<!DOCTYPE html>
<html lang="en">
<head>
<meta charset="utf-8">
<title>Brightmoor LLC</title>
<link href="https://fonts.googleapis.com/css2?family=Poppins:wght@400;500;600&family=Roboto:ital,wght@0,400;0,500;1,400&display=swap" rel="stylesheet">
<style>
:root{
  --blue:#0a56ad;
  --blue-dark:#0b4c9c;
  --ink:#333;
  --muted:#666;
  --light:#f5f5f5;
  --white:#fff;
}
*{box-sizing:border-box;margin:0;padding:0}
html,body{width:1200px;height:3822px;overflow:hidden}
body{font-family:'Roboto',Arial,sans-serif;color:var(--ink);background:#fff;position:relative}
a{color:inherit;text-decoration:none}

/* top bar */
.topbar{position:absolute;top:0;left:0;width:1200px;height:52px;background:var(--blue);color:#fff}
.social{position:absolute;left:111px;top:11px;display:flex;gap:6px}
.social span{width:31px;height:31px;border:1.5px solid #fff;border-radius:50%}
.topinfo{position:absolute;right:110px;top:16px;font-family:'Poppins',sans-serif;font-size:15px;display:flex;gap:34px}
.topinfo svg{vertical-align:-2px;margin-right:6px}

/* nav */
.nav{position:absolute;top:52px;left:0;width:1200px;height:107px;background:#fff;border-bottom:1px solid #e4e4e4}
.brand{position:absolute;left:111px;top:30px;display:flex;align-items:center;gap:12px}
.brand .dot{width:44px;height:44px;border-radius:50%;background:var(--blue)}
.brand .name{font-family:'Poppins',sans-serif;font-size:32px;color:var(--blue);line-height:1}
.menu{position:absolute;right:110px;top:45px;display:flex;gap:40px;font-family:'Poppins',sans-serif;font-size:15px;font-weight:500;color:#333}
.menu .on{color:var(--blue)}

/* hero */
.hero{position:absolute;top:159px;left:0;width:1200px;height:700px;overflow:hidden}
.hero-photo{position:absolute;inset:0;background:linear-gradient(180deg,#5c8fcf 0%,#8fb4de 22%,#3e70ae 34%,#2c5e9c 55%,#4d7d45 72%,#6c9a55 100%)}
.hero h1{position:absolute;top:66px;width:100%;text-align:center;font-family:'Poppins',sans-serif;font-weight:500;font-size:62px;color:#fff}
.hero p{position:absolute;top:152px;width:100%;text-align:center;font-family:'Poppins',sans-serif;font-size:29px;color:#fff}
.btn{display:inline-block;background:var(--blue);color:#fff;font-family:'Poppins',sans-serif;font-weight:500;border-radius:30px;text-align:center}
.hero .btn{position:absolute;left:511px;top:207px;width:178px;height:54px;line-height:54px;font-size:18px}
.hero svg.wave{position:absolute;left:0;bottom:0}
.dots{position:absolute;left:210px;top:630px;display:flex;gap:6px}
.dots i{width:11px;height:11px;border-radius:50%;background:#fff}
.dots i.on{background:var(--blue)}

/* about */
.about-k{position:absolute;top:910px;left:111px;font-family:'Poppins',sans-serif;font-size:21px;font-weight:500;color:#333}
.about-t{position:absolute;top:942px;left:111px;font-family:'Poppins',sans-serif;font-size:37px;font-weight:500;color:var(--blue)}
.about-p{position:absolute;left:111px;width:437px;font-size:13px;line-height:26px;color:#555;text-align:justify}
.about .btn{position:absolute;left:112px;top:1315px;width:151px;height:53px;line-height:53px;font-size:17px}
.about-ring{position:absolute;left:610px;top:861px;width:473px;height:473px;border-radius:50%;border:3px solid var(--blue)}
.about-img{position:absolute;left:10px;top:10px;right:10px;bottom:10px;border-radius:50%;background:linear-gradient(180deg,#2c7de0 0%,#5aa0ea 45%,#1d4d8a 60%,#2a5f9c 85%,#6a5f50 100%)}

/* section titles */
.stitle{position:absolute;width:1200px;text-align:center;font-family:'Poppins',sans-serif;font-size:35px;font-weight:500;color:#333;line-height:52px}
.stitle b{font-weight:500;color:var(--blue)}
.rule{position:absolute;left:577px;width:46px;height:3px;background:var(--blue)}

/* services */
.services{position:absolute;top:1421px;left:0;width:1200px;height:612px;background:var(--light)}
.svc{position:absolute;top:128px;width:252px;text-align:center}
.svc .ring{margin:0 auto;width:220px;height:220px;border-radius:50%;border:2px solid var(--blue);padding:6px}
.svc .ring div{width:100%;height:100%;border-radius:50%}
.svc h3{font-family:'Poppins',sans-serif;font-weight:500;font-size:19px;margin-top:18px;color:#222}
.svc p{font-size:13px;line-height:26px;color:#666;margin-top:10px;padding:0 14px;height:78px}
.svc .obtn{display:inline-block;margin-top:14px;width:147px;height:48px;line-height:44px;border:2px solid var(--blue);border-radius:25px;color:var(--blue);font-family:'Poppins',sans-serif;font-size:16px;background:#fff}

/* testimonials */
.testi{position:absolute;top:2033px;left:0;width:1200px;height:452px;background:linear-gradient(135deg,#1f6fc7,#2b82d6 45%,#1565bd);color:#fff;text-align:center}
.testi .stitle{color:#fff;top:33px}
.testi .rule{background:#fff;top:93px}
.avatar{position:absolute;left:539px;top:120px;width:122px;height:122px;border-radius:50%;background:linear-gradient(160deg,#8a6a55,#d9b7a0)}
.arrow{position:absolute;top:213px;width:44px;height:41px;border:1.5px solid #fff}
.arrow svg{position:absolute;left:15px;top:13px}
.quote{position:absolute;left:300px;width:600px;top:262px;font-style:italic;font-size:15px;line-height:28px}
.qm{font-family:Georgia,serif;font-size:46px;font-style:normal;font-weight:bold;line-height:0;vertical-align:-14px}
.who{position:absolute;top:365px;width:1200px;font-family:'Roboto',sans-serif;font-weight:500;font-size:15px}
.where{position:absolute;top:395px;width:1200px;font-size:13px;font-weight:500}

/* before after */
.ba{position:absolute;top:2625px;width:474px;height:309px;overflow:hidden}
.ba .half{position:absolute;top:0;width:236px;height:309px}
.ba .l{left:0}.ba .r{left:238px}
.ba .sep{position:absolute;left:236px;top:0;width:2px;height:309px;background:#fff}
.ba .knob{position:absolute;left:208px;top:126px;width:58px;height:58px;border-radius:50%;border:3px solid #fff}
.ba .label{position:absolute;bottom:18px;height:34px;line-height:34px;background:rgba(0,0,0,.55);color:#fff;font-family:'Poppins',sans-serif;font-weight:600;font-size:17px;letter-spacing:1px;padding:0 18px}

/* faq */
.faq{position:absolute;top:3004px;left:0;width:1200px;height:453px;background:linear-gradient(180deg,#f1f1f1,#fafafa)}
.q{position:absolute;width:454px;height:50px;background:#fff;border:1px solid #dcdcdc;font-family:'Poppins',sans-serif;font-size:14px;color:#333;line-height:48px;padding-left:15px}
.q::after{content:"+";position:absolute;right:14px;top:0;font-size:16px}
.q.open{background:var(--blue);color:#fff;border-color:var(--blue)}
.q.open::after{content:"–"}
.ans{position:absolute;width:454px;height:124px;background:#fff;border:1px solid #dcdcdc;border-top:none;font-size:12.5px;line-height:26px;color:#555;padding:16px 37px 0}

/* footer */
.footer{position:absolute;top:3457px;left:0;width:1200px;height:365px;background:var(--blue);color:#fff;text-align:center}
.fcol{position:absolute;top:40px;width:260px}
.fcol .ic{margin:0 auto;width:66px;height:66px;border-radius:50%;border:1.5px solid #fff;display:flex;align-items:center;justify-content:center}
.fcol h4{font-family:'Poppins',sans-serif;font-weight:600;font-size:17px;margin-top:16px}
.fcol p{font-size:13.5px;line-height:24px;margin-top:6px}
.fline{position:absolute;top:250px;left:110px;width:980px;height:1px;background:rgba(255,255,255,.18)}
.fbrand{position:absolute;left:130px;top:285px;display:flex;align-items:center;gap:12px}
.fbrand .dot{width:40px;height:40px;border-radius:50%;background:#fff}
.fbrand .name{font-family:'Poppins',sans-serif;font-size:30px;line-height:1}
.fmenu{position:absolute;right:108px;top:290px;display:flex;gap:52px;font-family:'Poppins',sans-serif;font-weight:500;font-size:14px}
.copy{position:absolute;left:658px;top:335px;font-family:'Poppins',sans-serif;font-size:14px}
</style>
</head>
<body>

<header class="topbar">
  <div class="social"><span></span><span></span><span></span><span></span></div>
  <div class="topinfo">
    <span><svg width="13" height="13" viewBox="0 0 24 24" fill="#fff"><path d="M6.6 10.8a15 15 0 0 0 6.6 6.6l2.2-2.2c.3-.3.7-.4 1-.2 1.1.4 2.3.6 3.6.6.6 0 1 .4 1 1V20c0 .6-.4 1-1 1A17 17 0 0 1 3 4c0-.6.4-1 1-1h3.5c.6 0 1 .4 1 1 0 1.3.2 2.5.6 3.6.1.3 0 .7-.2 1z"/></svg>(555) 014-2270</span>
    <span><svg width="12" height="15" viewBox="0 0 24 30" fill="#fff"><path d="M12 0C5.4 0 0 5.2 0 11.7 0 20.5 12 30 12 30s12-9.5 12-18.3C24 5.2 18.6 0 12 0zm0 16a4.5 4.5 0 1 1 0-9 4.5 4.5 0 0 1 0 9z"/></svg>4410 Birch Lane Shorewood, MN 55090</span>
  </div>
</header>

<nav class="nav">
  <div class="brand"><div class="dot"></div><div class="name">Brightmoor</div></div>
  <div class="menu"><a class="on">HOME</a><a>SERVICES</a><a>ABOUT US</a><a>CONTACT US</a><a>FAQS</a></div>
</nav>

<section class="hero">
  <div class="hero-photo" role="img" aria-label="Aerial view of a lake shoreline with white docks and boat lifts, trees and lawn"></div>
  <h1>Brightmoor LLC</h1>
  <p>Keeping Your Shoreline Clean and Pristine</p>
  <a class="btn">Read More</a>
  <svg class="wave" width="1200" height="300" viewBox="0 0 1200 300">
    <path d="M0 215 C150 330 330 300 520 220 C720 140 900 60 1200 120 L1200 300 L0 300Z" fill="var(--blue)"/>
    <path d="M0 245 C150 340 330 310 520 232 C720 155 900 80 1200 140 L1200 300 L0 300Z" fill="#fff"/>
  </svg>
  <div class="dots"><i></i><i class="on"></i><i></i></div>
</section>

<section class="about">
  <div class="about-k">ABOUT OUR</div>
  <div class="about-t">BRIGHTMOOR LLC</div>
  <p class="about-p" style="top:1007px">Brightmoor LLC is a company formed in response to the increasing incid ence of invasive species in Minnesota's lakes and water sys tems. The impact of these fast-growing nuisances, inspired our venture to effect ively control unwanted lake weeds. Brightmoor, LLC helps provide the enjoyable weed-free lake environment craved by water enthusiasts.</p>
  <p class="about-p" style="top:1162px">We have partnered with Green Loop Compost to recycle 100% of the lake weeds we remove. The types of materials used in compost have a huge impact on how long it takes to break down and how nutrient rich the end product will be. The lake weeds we provide have high levels of moisture as well as critically needed nitrogen.</p>
  <a class="btn">Read More</a>
  <div class="about-ring"><div class="about-img" role="img" aria-label="Dock with an empty boat lift canopy frame over blue lake water"></div></div>
</section>

<section class="services">
  <div class="stitle" style="top:32px">OUR <b>SERVICES</b></div>
  <div class="rule" style="top:88px"></div>
  <div class="svc" style="left:97px"><div class="ring"><div role="img" aria-label="Wheelbarrow full of removed lake weeds on the shore" style="background:linear-gradient(180deg,#bcd0e4,#6f8a4a 55%,#3d5a2c)"></div></div><h3>Lake Weed Removal</h3><p>Reclaim open water in front of your dock, beach, or boat slip removal method has teams</p><a class="obtn">Read More</a></div>
  <div class="svc" style="left:350px"><div class="ring"><div role="img" aria-label="Calm lake with a dock frame in the water" style="background:linear-gradient(180deg,#c7d3df,#8ea3b6 45%,#5f7587)"></div></div><h3>Zebra Mussel Removal</h3><p>This Invasive species is becoming an increasing risk to Minnesota these sharp mussels</p><a class="obtn">Read More</a></div>
  <div class="svc" style="left:602px"><div class="ring"><div role="img" aria-label="Rocky shoreline with dark debris along the water" style="background:linear-gradient(160deg,#7ea7d6,#9c8e74 40%,#1c2a4a 70%,#3d5f95)"></div></div><h3>Shoreline Cleanups</h3><p>Waves constantly litter trash, lake weeds, and other debris along your shoreline keep your beach</p><a class="obtn">Read More</a></div>
  <div class="svc" style="left:855px"><div class="ring"><div role="img" aria-label="Worker installing a dock on a blue lake" style="background:linear-gradient(180deg,#8fbbe8,#4f7b3c 35%,#2e5d9d 55%,#3a6fb0)"></div></div><h3>Beach Sanding</h3><p>Continuous waves wash away sand from your beach to expose mud &amp; larger rocks.</p><a class="obtn">Read More</a></div>
</section>

<section class="testi">
  <div class="stitle">TESTIMONIALS</div>
  <div class="rule"></div>
  <div class="avatar" role="img" aria-label="Customer portrait"></div>
  <div class="arrow" style="left:188px"><svg width="12" height="14" viewBox="0 0 12 14"><path d="M8 2 3 7l5 5" stroke="#fff" stroke-width="1.6" fill="none"/></svg></div>
  <div class="arrow" style="left:967px"><svg width="12" height="14" viewBox="0 0 12 14"><path d="M4 2l5 5-5 5" stroke="#fff" stroke-width="1.6" fill="none"/></svg></div>
  <p class="quote"><span class="qm">&ldquo;</span> Everyone used to jump off the water trampoline and instantly get tangled in lake weeds. We contacted Brightmoor and their SCUBA divers have now been solving our problem for the past 4 years! <span class="qm">&rdquo;</span></p>
  <div class="who">– WILLOW BAY HOMEOWNERS ASSOCIATION</div>
  <div class="where">(LAKE ARDENWOOD)</div>
</section>

<section class="beforeafter">
  <div class="stitle" style="top:2525px">BEFORE &amp; AFTER</div>
  <div class="rule" style="top:2581px"></div>
  <div class="ba" style="left:111px">
    <div class="half l" role="img" aria-label="Shallow water choked with lake weeds before cleanup" style="background:linear-gradient(180deg,#a9b3bd,#7c7a63 45%,#8d7d58)"></div>
    <div class="half r" role="img" aria-label="Clear lake water with dock frame after cleanup" style="background:linear-gradient(180deg,#cdd5dd,#9ea9b2 40%,#56626c)"></div>
    <div class="sep"></div><div class="knob"></div>
    <div class="label" style="left:0">BEFORE</div><div class="label" style="right:0">AFTER</div>
  </div>
  <div class="ba" style="left:615px">
    <div class="half l" role="img" aria-label="Wooden dock covered in weeds before cleanup" style="background:linear-gradient(180deg,#4f7a3c,#6d8f4f 40%,#8c7f6a)"></div>
    <div class="half r" role="img" aria-label="Clean wooden dock among reeds after cleanup" style="background:linear-gradient(180deg,#4c7636,#74985a 40%,#a89a84)"></div>
    <div class="sep"></div><div class="knob"></div>
    <div class="label" style="left:0">BEFORE</div><div class="label" style="right:0">AFTER</div>
  </div>
</section>

<section class="faq">
  <div class="stitle" style="top:48px">OUR <b>FAQ'S</b></div>
  <div class="rule" style="top:104px"></div>
  <div class="q" style="left:128px;top:134px">Q . How early do lake weeds start to grow?</div>
  <div class="q open" style="left:128px;top:194px">Q . How fast do lake weeds grow?</div>
  <div class="ans" style="left:128px;top:244px">Eurasian Water Milfoil can grow up to two (2) inches per day and can quickly form dense mats that block out other native plants! Warm water temperatures and an abundance</div>
  <div class="q" style="left:615px;top:134px">Q . How big of an area can I treat?</div>
  <div class="q" style="left:615px;top:194px">Q . What if the treatment area encroaches?</div>
  <div class="q" style="left:615px;top:255px">Q . How long does each treatment last?</div>
  <div class="q" style="left:615px;top:316px">Q . I DO NOT have a natural beach. Can I install one?</div>
</section>

<footer class="footer">
  <div class="fcol" style="left:153px"><div class="ic"><svg width="14" height="18" viewBox="0 0 24 30" fill="#fff"><path d="M12 0C5.4 0 0 5.2 0 11.7 0 20.5 12 30 12 30s12-9.5 12-18.3C24 5.2 18.6 0 12 0zm0 16a4.5 4.5 0 1 1 0-9 4.5 4.5 0 0 1 0 9z"/></svg></div><h4>LOCATION</h4><p>4410 Birch Lane<br>Shorewood, MN 55090</p></div>
  <div class="fcol" style="left:485px"><div class="ic"><svg width="17" height="17" viewBox="0 0 24 24" fill="#fff"><path d="M6.6 10.8a15 15 0 0 0 6.6 6.6l2.2-2.2c.3-.3.7-.4 1-.2 1.1.4 2.3.6 3.6.6.6 0 1 .4 1 1V20c0 .6-.4 1-1 1A17 17 0 0 1 3 4c0-.6.4-1 1-1h3.5c.6 0 1 .4 1 1 0 1.3.2 2.5.6 3.6.1.3 0 .7-.2 1z"/></svg></div><h4>CONTACT</h4><p>(555) 014-2270</p></div>
  <div class="fcol" style="left:816px"><div class="ic"><svg width="18" height="14" viewBox="0 0 24 18" fill="#fff"><path d="M0 0h24v2L12 10 0 2zM0 5l12 8 12-8v13H0z"/></svg></div><h4>EMAIL</h4><p>info@brightmoor.example</p></div>
  <div class="fline"></div>
  <div class="fbrand"><div class="dot"></div><div class="name">Brightmoor</div></div>
  <div class="fmenu"><a>HOME</a><a>SERVICES</a><a>ABOUT US</a><a>CONTACT US</a><a>FAQ</a></div>
  <div class="copy">© Copyright 2022 Brightmoor.All rights reserved.</div>
</footer>

</body>
</html>
```